Kestrel Finish Studio (KFS)

I would like to design a dedicated site for my KFS product, which allows industry employees to be trained in the visual inspection of mechanical parts. My product is a 3D simulator (see https://morvint-works.ch/our-applications/virtual-reality/ and https://morvint-works.ch for videos) which makes it possible to manufacture standard parts representative of a type of defect which is accepted or refused by the quality department. These master parts can be used to create a common quality culture in the company and to train employees in a homogeneous way. The simulator is initially designed for watchmaking, but must be designed for much broader industries (cars, phone reconditioning, ball bearings, etc.)
L'information que j'ai donnée n'est pas assez précise. Je dois préciser les domaines métiers visés par le site internet. J'ai besoin de quelques jours pour choisir les domaines les plus représentatifs.
Coded - Design and coding required
1 page

```html
<!DOCTYPE html>
<html lang="en">
<head>
<meta charset="utf-8">
<title>Kestrel Finish Studio</title>
<link href="https://fonts.googleapis.com/css2?family=Michroma&family=Poppins:wght@400;500;600&display=swap" rel="stylesheet">
<style>
:root{
  --blue:#1f5fc0;
  --blue-bright:#2c6fd6;
  --navy:#1a1d2b;
  --ink:#1b2333;
  --text:#3a3f4a;
  --muted:#5b6270;
  --pale:#e6eef8;
  --white:#fff;
  --head:'Michroma',sans-serif;
  --body:'Poppins',sans-serif;
}
*{box-sizing:border-box;margin:0;padding:0}
html,body{width:1200px;height:4161px;overflow:hidden}
body{position:relative;font-family:var(--body);color:var(--text);background:var(--white)}
.abs{position:absolute}
section,header,footer{position:absolute;left:0;width:1200px;overflow:hidden}
a{color:inherit;text-decoration:none}
.btn{position:absolute;background:var(--blue);color:#fff;font-family:var(--head);font-size:15px;display:flex;align-items:center;justify-content:center;border-radius:3px}

/* header */
.site-header{top:0;height:104px;background:#fff}
.topbar{position:absolute;left:331px;top:0;width:869px;height:36px;background:var(--navy);clip-path:polygon(0 0,100% 0,100% 100%,14px 100%)}
.topbar .item{position:absolute;top:8px;color:#fff;font-size:14px;display:flex;align-items:center;gap:14px}
.topbar .dot{width:24px;height:24px;border-radius:50%;background:var(--blue-bright);display:flex;align-items:center;justify-content:center}
.search{position:absolute;left:567px;top:6px;width:200px;height:26px;background:#fff;border-radius:13px}
.search .dot{position:absolute;right:3px;top:3px;width:20px;height:20px}
.brand{position:absolute;left:92px;top:30px;width:215px;text-align:center;font-family:var(--head);font-size:21px;line-height:28px;color:var(--ink)}
.nav{position:absolute;left:347px;top:63px;display:flex;gap:30px;font-size:15px;color:var(--text)}
.nav .active{color:var(--blue)}
.contact-btn{left:959px;top:57px;width:137px;height:37px;font-size:17px}

/* hero */
.hero{top:104px;height:560px;background:linear-gradient(110deg,#0d2a55 0%,#1b4d8e 40%,#2b7fc4 62%,#7fd0f0 75%,#1d5a9a 100%)}
.hero-title{left:103px;top:208px;font-family:var(--head);font-size:36px;line-height:42px;color:#fff}
.hero-sub{left:103px;top:305px;width:430px;font-size:17px;line-height:29px;color:#fff}
.hero .btn{left:103px;top:381px;width:167px;height:38px}
.arrow{position:absolute;top:270px;width:20px;height:20px;border-radius:50%;background:#fff}

/* control */
.control{top:664px;height:457px}
.h-blue{font-family:var(--head);color:var(--blue)}
.control h2{position:absolute;left:0;width:1200px;top:60px;text-align:center;font-size:30px;line-height:37px;font-weight:400}
.col{position:absolute;top:167px;width:490px;font-size:14px;line-height:22px}
.col p{margin-bottom:19px}
.divider{position:absolute;left:591px;top:163px;width:2px;height:197px;background:#c9ccd2}

/* allows */
.allows{top:1121px;height:488px;background:var(--navy)}
.photo-left{left:0;top:0;width:700px;height:488px;background:linear-gradient(120deg,#8a8d92,#4d5056 55%,#2b2d33);clip-path:polygon(0 0,575px 0,695px 100%,0 100%)}
.allows h2{left:640px;top:52px;font-size:28px;font-weight:400}
.allows p{position:absolute;color:#fff;font-size:14.5px;line-height:26px}

/* lighten */
.lighten{top:1609px;height:651px}
.pale-panel{left:635px;top:0;width:565px;height:651px;background:var(--pale)}
.lighten h2{left:102px;top:114px;font-size:32px;line-height:43px;font-weight:400}
.lighten p{position:absolute;left:102px;top:257px;width:428px;font-size:14.5px;line-height:23px;text-align:justify}
.lighten .btn{left:103px;top:468px;width:164px;height:40px}
.frame{position:absolute;border:8px solid #fff;box-shadow:0 2px 8px rgba(0,0,0,.12)}

/* quote */
.quote{top:2260px;height:235px;background:var(--blue)}
.quote p{position:absolute;left:70px;top:56px;width:1060px;text-align:center;color:#fff;font-family:var(--head);font-size:20px;line-height:30px}

/* awareness */
.awareness{top:2495px;height:488px;background:var(--navy)}
.awareness h2{left:108px;top:96px;font-size:29px;line-height:38px;font-weight:400}
.awareness p{position:absolute;left:108px;top:230px;width:455px;color:#fff;font-size:14.5px;line-height:26px}
.photo-right{left:673px;top:0;width:527px;height:488px;background:linear-gradient(200deg,#95989d,#54575d 50%,#26282d)}

/* features */
.features{top:2983px;height:761px}
.tablet{position:absolute;top:74px;height:318px;border-radius:22px;background:#e9eaec;box-shadow:0 3px 10px rgba(0,0,0,.25)}
.tablet .screen{position:absolute;left:26px;top:14px;right:18px;bottom:14px;border-radius:6px;background:linear-gradient(90deg,#2a3856 0 35%,#3a2a1c 35%,#8a5a22 70%,#2a1f16)}
.tablet.table .screen{background:linear-gradient(180deg,#23304f,#1a2540)}
.tag{position:absolute;height:45px;background:var(--blue-bright);color:#fff;font-size:17px;display:flex;align-items:center;justify-content:center;letter-spacing:.5px}
.tag.right{clip-path:polygon(0 0,92% 0,100% 50%,92% 100%,0 100%)}
.tag.left{clip-path:polygon(8% 0,100% 0,100% 100%,8% 100%,0 50%)}
.feature h3{position:absolute;top:415px;width:500px;text-align:center;font-family:var(--head);font-weight:400;font-size:26px;line-height:36px;color:var(--ink)}
.feature p{position:absolute;top:489px;width:460px;text-align:center;font-size:14.5px;line-height:22.5px;color:var(--muted)}

/* footer */
.site-footer{top:3744px;height:417px;background:var(--navy);color:#fff}
.f-brand{left:102px;top:86px;font-size:22px;line-height:30px;color:var(--blue-bright)}
.f-tag{position:absolute;left:106px;top:158px;width:225px;font-size:13px;line-height:23px}
.social{position:absolute;top:219px;width:28px;height:28px;border:1.5px solid #fff;border-radius:50%}
.f-col{position:absolute;top:88px}
.f-col h4{font-family:var(--head);font-weight:400;font-size:18px;margin-bottom:14px}
.f-col li{list-style:none;font-size:14px;line-height:24px}
.c-row{display:flex;gap:14px;font-size:14px;line-height:20px;margin-bottom:14px}
.c-icon{width:24px;height:24px;flex:none;border:1.5px solid #fff;border-radius:50%}
.f-line{position:absolute;left:102px;top:4073px;width:915px;height:1px;background:#3b4052}
.copy{position:absolute;left:0;width:1200px;top:366px;text-align:center;font-size:12px}
</style>
</head>
<body>

<header class="site-header">
  <div class="topbar">
    <div class="item" style="left:73px"><span class="dot"><svg width="12" height="12" viewBox="0 0 12 12"><path d="M6 1a3.5 3.5 0 0 0-3.5 3.5C2.5 7.5 6 11 6 11s3.5-3.5 3.5-6.5A3.5 3.5 0 0 0 6 1z" fill="#fff"/></svg></span>+41 79 000 12 34</div>
    <div class="item" style="left:254px"><span class="dot"><svg width="12" height="10" viewBox="0 0 12 10"><rect x="1" y="1" width="10" height="8" fill="none" stroke="#fff"/><path d="M1 1l5 4 5-4" fill="none" stroke="#fff"/></svg></span>info@kestrelfinishstudio.com</div>
    <div class="search"><span class="dot topbar-dot" style="background:var(--blue-bright);border-radius:50%;display:block"></span></div>
  </div>
  <div class="brand">Kestrel Finish<br>Studio</div>
  <nav class="nav">
    <a class="active">Home</a><a>About</a><a>In regards to Services</a><a>Partners</a><a>References</a><a>Info</a>
  </nav>
  <a class="btn contact-btn">Contact Us</a>
</header>

<section class="hero" role="img" aria-label="Engineer with a VR headset inspecting a glowing wireframe car">
  <div class="abs hero-title">KESTREL FINISH<br>STUDIO</div>
  <div class="abs hero-sub">Virtual Reality At The Service Of Controlled Aesthetic Watchmaking</div>
  <a class="btn">GET STARTED</a>
  <span class="arrow" style="left:30px"></span>
  <span class="arrow" style="left:1129px"></span>
</section>

<section class="control">
  <h2 class="h-blue">AESTHETIC CONTROL: HOW TO<br>CONTROL IT?</h2>
  <div class="col" style="left:90px">
    <p>Adopting a simple and unambiguous language for a common understanding of aesthetic quality at the extended enterprise level.</p>
    <p>By using a semantic reference matrix associating the types of anomalies (scratches, marks, deformations, stains, etc.) with the intensity levels defined with the company.</p>
    <p>Determining the compliance thresholds of the component<br>or product.</p>
  </div>
  <div class="divider"></div>
  <div class="col" style="left:641px">
    <p>Providing uniform training in operational competence for those responsible for aesthetic control.</p>
    <p>By regularly assessing the competence to measure the aesthetics, expressed in a tangible, reliable and sustainable way (R&amp;R), of a component or product.</p>
    <p>By designing realistic and attractive teaching sequences for total quality control.</p>
  </div>
</section>

<section class="allows">
  <div class="abs photo-left" role="img" aria-label="Watchmaker with a loupe examining a small part"></div>
  <h2 class="abs h-blue">KFS Allows:</h2>
  <p style="left:640px;top:97px;width:480px">Remove the management of components used as standards for aesthetic control training</p>
  <p style="left:670px;top:158px;width:420px">To make employees aware of aesthetic control and the vocabulary to be used</p>
  <p style="left:703px;top:218px;width:440px">Integrate aesthetic control into a total quality management (TQM) approach with precise indicators at all stages of the manufacturing and after-sales processes</p>
  <p style="left:756px;top:310px;width:360px">Provide the after-sales service with an efficient tool to record the aesthetic aspect of the supported product</p>
</section>

<section class="lighten">
  <div class="abs pale-panel"></div>
  <h2 class="abs h-blue">Lighten The<br>Management Of<br>Physical Components</h2>
  <p>Companies must manage and maintain sets of physical components used as a 'yardstick' for the training of aesthetic testers. The cost of managing a set of physical parts representing all combinations of shapes, defect types, materials and finishes is very high. KFS allows the company to significantly reduce its management burden by scanning components or products in 3D and then virtually adding 'typical' aesthetic anomalies.</p>
  <a class="btn">LEARN MORE</a>
  <div class="frame" style="left:630px;top:67px;width:320px;height:236px;background:linear-gradient(135deg,#2a1d10,#b98a3c 45%,#1c140c)" role="img" aria-label="Close-up of a gold watch case ring"></div>
  <div class="frame" style="left:855px;top:182px;width:322px;height:249px;background:linear-gradient(135deg,#b9bcc0,#5a5d63 60%,#303237)" role="img" aria-label="Hands holding a watch movement with tweezers"></div>
  <div class="frame" style="left:690px;top:277px;width:323px;height:251px;background:linear-gradient(160deg,#7a8696,#3f6f99 55%,#1e2d44)" role="img" aria-label="Car model inside a scanning station"></div>
</section>

<section class="quote">
  <p>"In the implementation of the new Qualiticien-nes en microtechnique course, the Lakeside School of Watchmaking has deployed the KFS application to teach the methods of aesthetic control. This application fully meets the pedagogical objectives as well as the ease of use by both our teaching staff and our students."</p>
</section>

<section class="awareness">
  <h2 class="abs h-blue">Raising awareness<br>of criteria and aesthetic<br>vocabulary</h2>
  <p>Aesthetic defects are often the result of careless handling of the components and products concerned, whether during manufacture, assembly or marketing. By making the KFS platform available to staff in direct contact with the product, it becomes very easy to make them aware of the evaluation criteria and the aesthetic vocabulary defined by the company.</p>
  <div class="abs photo-right" role="img" aria-label="Hands holding a watch movement under inspection"></div>
</section>

<section class="features">
  <div class="tablet" style="left:105px;width:486px"><div class="screen" role="img" aria-label="Simulator interface with settings panel and a watch case view"></div></div>
  <div class="tablet table" style="left:606px;width:492px"><div class="screen" role="img" aria-label="Semantic matrix table of defect types and intensities"></div></div>
  <div class="tag right" style="left:433px;top:186px;width:326px">A SEMANTIC MATRIX</div>
  <div class="tag left" style="left:436px;top:257px;width:323px">AN INTUITIVE INTERFACE ...</div>
  <div class="feature">
    <h3 style="left:81px">IMPROVE AFTER-SALES<br>SERVICE RETURNS</h3>
    <p style="left:101px">The KFS platform can easily be used by the service network staff to assist them in the objective assessment of aesthetic defects by referring to the semantic matrix as well as to the cases already referenced. It is also possible, in an intuitive and playful way, to indicate, in accordance with the product nomenclature, a type of imperfection, its intensity and its location. It is also possible to draw up a precise repair estimate or to declare a non-conformity on a product coming from a market return.</p>
  </div>
  <div class="feature">
    <h3 style="left:601px">IMPROVING THE TOTAL<br>QUALITY APPROACH</h3>
    <p style="left:621px">During the entire product life cycle, from design through customer service to distribution, the KFS application makes it possible to build up a database of aesthetic defects in a simple, efficient and computerised way. On this basis of consolidated data, it is then possible to establish recurrences, such as potential correlations, thus enabling solutions to be found to correct, improve and optimise the product, process or service offer.</p>
  </div>
</section>

<footer class="site-footer">
  <div class="abs f-brand h-blue">Kestrel Finish<br>Studio</div>
  <p class="f-tag">Connecting machines, users and data.</p>
  <span class="social" style="left:106px"></span>
  <span class="social" style="left:146px"></span>
  <span class="social" style="left:188px"></span>
  <span class="social" style="left:228px"></span>
  <div class="f-col" style="left:420px">
    <h4>Use Link</h4>
    <ul><li>Home</li><li>About</li><li>In regards to Services</li><li>Partners</li><li>References</li><li>Info</li><li>Contact Us</li></ul>
  </div>
  <div class="f-col" style="left:610px">
    <h4>Help Link</h4>
    <ul><li>Terms&amp;condtions</li><li>Privacy Policy</li><li>Support</li><li>Blog</li></ul>
  </div>
  <div class="f-col" style="left:820px">
    <h4>Contact Us</h4>
    <div class="c-row"><span class="c-icon"></span><span>+41 79 000 12 34<br>+41 79 000 56 78</span></div>
    <div class="c-row"><span class="c-icon"></span><span>info@kestrelfinishstudio.com</span></div>
    <div class="c-row"><span class="c-icon"></span><span>Lorem ipsum dolor sit amet,<br># 640, Col.adipiscing eiusmod</span></div>
  </div>
  <div class="copy">2023 © Kestrel Finish Studio | All Rights Reserved</div>
</footer>
<div class="f-line"></div>

</body>
</html>
```